Book Cover for Lanterns Along the Quiet Threshold

I need a book cover for a 6 x 9 paperback titled Lanterns Along the Quiet Threshold Gathered from Research and Voices Dwelling in the Realm beyond Our Present Days. It has to do with consciousness, the mind, incarnation onto Earth, leaving Earth, and the life in the life after this life. I have an idea I'm providing with this description, but I am open to anything that would be striking and stimulating, whether with a book or not. I am the author, T. Morgan Wexley. I've added another background idea to see if anyone can do something with it and I've increased the budget.

```html
<!DOCTYPE html>
<html lang="en">
<head>
<meta charset="utf-8">
<title>Lanterns Along the Quiet Threshold — Book Cover</title>
<link href="https://fonts.googleapis.com/css2?family=Exo+2:wght@300;600;700&display=swap" rel="stylesheet">
<style>
  :root {
    --backdrop: #7d7d7f;
    --space-dark: #1c0d1e;
    --space-plum: #3a1426;
    --ember-red: #8a2a1c;
    --glow-orange: #e0782e;
    --glow-core: #f7c77a;
    --earth-slate: #6a6a70;
    --earth-deep: #2a2a30;
    --paper-white: #f4f4f6;
    --emblem-edge: #140a0c;
    --ink-dark: #241418;
    --title-white: #ffffff;
  }
  * { margin: 0; padding: 0; box-sizing: border-box; }
  html, body {
    width: 1200px; height: 1200px; overflow: hidden;
    background: var(--backdrop);
    font-family: "Exo 2", sans-serif;
  }
  .canvas { position: relative; width: 1200px; height: 1200px; }
  .book-cover {
    position: absolute; left: 240px; top: 60px;
    width: 720px; height: 1080px; overflow: hidden;
    box-shadow: 0 14px 30px rgba(0,0,0,0.35);
  }
  .cover-scene {
    position: absolute; inset: 0;
    background:
      radial-gradient(ellipse 6% 55% at 50% 60%, rgba(247,199,122,0.5), transparent 70%),
      radial-gradient(ellipse 60% 42% at 50% 80%, var(--glow-core) 0%, var(--glow-orange) 30%, var(--ember-red) 65%, transparent 100%),
      linear-gradient(180deg, var(--space-dark) 0%, var(--space-plum) 30%, var(--ember-red) 62%, var(--space-plum) 100%);
  }
  .cover-planet {
    position: absolute; left: -260px; top: 895px;
    width: 1240px; height: 700px; border-radius: 50%;
    background: radial-gradient(ellipse at 50% 10%, var(--earth-slate) 0%, var(--earth-deep) 45%);
    box-shadow: 0 -10px 30px rgba(247,199,122,0.35);
  }
  .emblem { position: absolute; left: 0; top: 0; width: 720px; height: 1080px; }
  .cover-title {
    position: absolute; left: 65px; top: 278px;
    color: var(--title-white);
    font-weight: 600; font-size: 31px; line-height: 40px;
    letter-spacing: 0.06em; text-transform: uppercase;
  }
  .cover-subtitle {
    position: absolute; left: 40px; right: 40px; top: 826px;
    text-align: center; color: var(--ink-dark);
    font-weight: 300; font-size: 25px; line-height: 32px;
  }
  .cover-author {
    position: absolute; left: 0; right: 0; top: 1000px;
    text-align: center; color: var(--title-white);
    font-weight: 600; font-size: 40px;
  }
</style>
</head>
<body>
<main class="canvas">
  <section class="book-cover">
    <div class="cover-scene" role="img" aria-label="Deep space with a bright orange burst of light rising above the horizon"></div>
    <div class="cover-planet" role="img" aria-label="Curve of planet Earth seen from space"></div>
    <svg class="emblem" viewBox="0 0 720 1080" role="img" aria-label="Large white question mark">
      <g transform="translate(-9 6)" fill="var(--emblem-edge)">
        <path d="M110 255 C110 120 230 33 380 33 C540 33 635 140 635 280 C635 400 565 470 475 500 L432 515 L432 591 L290 591 L290 520 C290 440 360 370 410 310 C440 270 462 235 462 200 C462 158 425 128 380 128 C318 128 270 172 265 255 Z"/>
        <circle cx="346" cy="709" r="86"/>
      </g>
      <g fill="var(--paper-white)">
        <path d="M110 255 C110 120 230 33 380 33 C540 33 635 140 635 280 C635 400 565 470 475 500 L432 515 L432 591 L290 591 L290 520 C290 440 360 370 410 310 C440 270 462 235 462 200 C462 158 425 128 380 128 C318 128 270 172 265 255 Z"/>
        <circle cx="346" cy="709" r="86"/>
      </g>
    </svg>
    <h1 class="cover-title">Lanterns<br>Along the<br>Quiet<br>Threshold</h1>
    <p class="cover-subtitle">Gathered from Research and Voices Dwelling<br>in the Realm beyond Our Present Days</p>
    <p class="cover-author">T. Morgan Wexley</p>
  </section>
</main>
</body>
</html>
```